SOLVE Study flyer

I need help designing a flyer for a research study that will include brain imaging in adolescents. The info is in the attached document. The study is called the Sequoia Outlook Lantern Valley Echo (SOLVE) study. Ideally this would be returned as a document that I can edit in the future as we will have several new recruitment phases (different age groups, etc. I also would love to have a logo designed as part of this project, but I recognize that might be a separate design request.

```html
<!DOCTYPE html>
<html lang="en">
<head>
<meta charset="utf-8">
<title>SOLVE Study – Recruitment Flyer</title>
<link href="https://fonts.googleapis.com/css2?family=Figtree:ital,wght@0,400;0,500;0,600;0,700;0,800;1,500&display=swap" rel="stylesheet">
<style>
  :root{
    --navy:#0e2457;
    --purple:#5b2d8e;
    --purple-soft:#e6dcef;
    --teal:#17a2a0;
    --teal-light:#73d0c9;
    --teal-dark:#0e7f7a;
    --teal-wash:#f1f8f7;
    --blue-soft:#d7e0f0;
    --ink:#1b1f2a;
    --white:#ffffff;
  }
  *{box-sizing:border-box;margin:0;padding:0}
  html,body{width:953px;height:1200px;overflow:hidden;background:var(--white)}
  body{font-family:"Figtree",Arial,sans-serif;color:var(--ink)}
  .flyer{position:relative;width:953px;height:1200px;background:var(--white)}
  .abs{position:absolute}

  /* header */
  .header-art{left:92px;top:102px;width:761px;height:237px;
    background:linear-gradient(100deg,#f4f7fa 0%,#eceff3 35%,#f3efe6 60%,#efe4f3 80%,#e9eff7 100%)}
  .hero-photo{left:563px;top:102px;width:290px;height:430px;
    background:linear-gradient(160deg,#efe3dd 0%,#c7a596 30%,#9b7ec9 60%,#7f5fb8 100%)}
  .brand-mark{left:130px;top:150px;width:132px;height:132px;border-radius:50%;background:var(--navy)}
  .brand-name{left:290px;top:180px;font-size:50px;font-weight:800;color:var(--navy);line-height:1}
  .brand-full{left:292px;top:244px;width:260px;font-size:17px;font-weight:500;color:var(--purple);line-height:23px}

  .circle-photo{border-radius:50%;border:4px solid var(--white)}
  .circle-chip{left:646px;top:332px;width:214px;height:214px;
    background:radial-gradient(circle at 50% 40%,#9fc7f2 0%,#4c58c8 35%,#5a2c9a 75%,#2a1f6e 100%)}
  .circle-head{left:551px;top:448px;width:130px;height:130px;
    background:radial-gradient(circle at 55% 40%,#e7c7a7 0%,#a9848c 40%,#4b4f78 80%,#2c3052 100%)}

  /* question band */
  .question-band{left:92px;top:339px;width:482px;height:182px;background:var(--navy);color:var(--white)}
  .q-parent{left:49px;top:14px;font-size:28px;font-weight:700;line-height:34px}
  .q-parent .age{color:var(--teal-light);font-size:36px;font-weight:700}
  .q-divider{left:50px;top:93px;width:276px;height:1px;background:#6f6aa8}
  .q-dots{left:336px;top:89px;display:flex;gap:11px}
  .q-dots span{width:8px;height:8px;border-radius:50%}
  .q-worry{left:49px;top:106px;font-size:28px;font-weight:700;line-height:29px;color:var(--teal-light)}

  .intro{left:128px;top:535px;width:390px;border-left:2px solid var(--teal-light);
    padding-left:19px;font-size:15.5px;line-height:19.5px;padding-top:2px}
  .intro strong{color:var(--purple);font-weight:800}

  /* participation */
  .participation{left:124px;top:650px;width:454px;height:239px;border:1.5px solid var(--purple);border-radius:14px}
  .pill-label{left:198px;top:637px;width:290px;height:28px;border-radius:14px;background:var(--purple);
    color:var(--white);font-size:15px;font-weight:800;text-align:center;line-height:28px;letter-spacing:.2px}
  .step{top:677px;width:140px;text-align:center;font-size:11px;line-height:13px}
  .step-icon{width:80px;height:80px;border-radius:50%;margin:0 auto 11px;display:flex;align-items:center;justify-content:center}
  .step-title{font-weight:800;font-size:11px;line-height:13px}
  .step-divider{top:684px;width:1px;height:192px;background:#cdbfdc}

  /* eligibility */
  .eligibility{left:595px;top:599px;width:227px;height:292px;border:1.5px solid var(--teal-light);
    border-radius:16px;background:var(--teal-wash)}
  .elig-icon{left:676px;top:568px;width:70px;height:70px;border-radius:50%;background:var(--white);
    border:1.5px solid var(--teal-light);display:flex;align-items:center;justify-content:center}
  .elig-title{left:617px;top:651px;font-size:16.5px;font-weight:800;color:var(--teal-dark);line-height:21px;letter-spacing:.2px}
  .elig-rule{left:617px;top:697px;width:188px;height:1.5px;background:var(--teal-dark)}
  .elig-list{left:622px;top:708px;width:155px;list-style:none;font-size:14px;line-height:16px}
  .elig-list li{position:relative;padding-left:22px;margin-bottom:16px}
  .elig-list li svg{position:absolute;left:0;top:1px}

  /* contact + compensation */
  .contact-ring{left:128px;top:915px;width:68px;height:68px;border-radius:50%;border:1.5px solid var(--purple);
    display:flex;align-items:center;justify-content:center}
  .contact-ring .inner{width:58px;height:58px;border-radius:50%;background:var(--purple);display:flex;align-items:center;justify-content:center}
  .contact-text{left:214px;top:919px;font-size:15px;font-weight:800;color:var(--purple);line-height:19px}
  .contact-text .second{color:var(--navy)}
  .contact-text em{display:block;font-style:italic;font-weight:500;font-size:16px;color:var(--teal-dark);margin-top:2px}
  .contact-divider{left:483px;top:916px;width:1px;height:72px;background:#cfc8dc}
  .comp-pill{left:538px;top:916px;width:284px;height:69px;border-radius:0 35px 35px 0;background:var(--navy)}
  .gift-ring{left:499px;top:911px;width:78px;height:78px;border-radius:50%;background:var(--white);
    border:1.5px solid var(--navy);display:flex;align-items:center;justify-content:center}
  .comp-text{left:607px;top:925px;color:var(--white);font-size:18.5px;font-weight:700;line-height:22px}
  .comp-line{display:block}
  .comp-line + .comp-line{display:flex;align-items:baseline;gap:8px;margin-top:0}
  .comp-text .amount{color:var(--teal-light);font-size:37px;font-weight:800;line-height:34px}

  /* footer */
  .footer{left:92px;top:1007px;width:761px;height:80px;
    background:linear-gradient(90deg,#5a3293 0%,#1d2a66 45%,#113e70 65%,#46bdb8 100%)}
  .footer-email{left:57px;top:28px;display:flex;align-items:center;gap:7px;color:var(--white);font-size:19px;font-weight:500}
  .footer-icons{left:478px;top:10px;display:flex;align-items:center;gap:14px}
  .footer-icons .sep{width:1px;height:16px;border-left:1px dotted rgba(255,255,255,.7)}
  .footer-note{left:420px;top:39px;width:300px;text-align:center;color:var(--white);font-size:11px;line-height:13px}
</style>
</head>
<body>
<main class="flyer">

  <div class="abs header-art" role="img" aria-label="Soft backdrop of a faint brain illustration with handwritten maths formulas and light streaks"></div>
  <div class="abs hero-photo" role="img" aria-label="Photo of a thoughtful teenage girl in a purple hoodie looking upward"></div>

  <div class="abs brand-mark" aria-hidden="true"></div>
  <h1 class="abs brand-name">SOLVE Study</h1>
  <p class="abs brand-full">Sequoia Outlook Lantern Valley Echo</p>

  <section class="abs question-band">
    <p class="abs q-parent">Are you the parent of a child<br>age <span class="age">10-17?</span></p>
    <div class="abs q-divider"></div>
    <div class="abs q-dots"><span style="background:#9b7fd1"></span><span style="background:var(--teal-light)"></span><span style="background:#f2c98c"></span></div>
    <p class="abs q-worry">Do they worry or overthink<br>negative emotions?</p>
  </section>

  <div class="abs circle-photo circle-chip" role="img" aria-label="Illustration of a glowing brain rising from a circuit board"></div>
  <div class="abs circle-photo circle-head" role="img" aria-label="Illustration of a profile head with a glowing network brain"></div>

  <p class="abs intro">Lantern Valley University researchers are seeking <strong>girls age 10-17</strong> for a study about brain activity in emotions and decision-making and how they relate to puberty, anxiety and depression.</p>

  <section class="abs participation"></section>
  <div class="abs pill-label">STUDY PARTICIPATION INVOLVES:</div>

  <div class="abs step" style="left:126px">
    <div class="step-icon" style="background:var(--purple-soft)">
      <svg width="46" height="46" viewBox="0 0 46 46" fill="none" stroke="#5b2d8e" stroke-width="1.6" stroke-linejoin="round">
        <rect x="3" y="5" width="14" height="10" rx="2"/><rect x="14" y="2" width="14" height="9" rx="2"/>
        <circle cx="14" cy="26" r="5"/><path d="M5 42v-4a9 9 0 0 1 18 0v4z"/>
        <circle cx="32" cy="23" r="5"/><path d="M24 42v-5a8 8 0 0 1 16 0v5z"/><path d="M21 35h22v4H21z"/>
      </svg>
    </div>
    <div class="step-title" style="color:var(--purple)">ONE ONE-HOUR<br>INTERVIEW</div>
    (online or in-person)<br>where your child will<br>discuss their thoughts.
  </div>

  <div class="step-divider abs" style="left:272px"></div>

  <div class="abs step" style="left:276px">
    <div class="step-icon" style="background:#cdebe8">
      <svg width="50" height="46" viewBox="0 0 50 46" fill="none" stroke="#17a2a0" stroke-width="1.8" stroke-linejoin="round">
        <rect x="3" y="8" width="40" height="27" rx="2"/><path d="M3 30h40M19 35l-2 6h12l-2-6M13 42h20"/>
        <circle cx="40" cy="9" r="7" fill="#cdebe8"/><path d="M37 9l2 2 4-4"/>
      </svg>
    </div>
    <div class="step-title" style="color:var(--teal)">ONLINE<br>QUESTIONNAIRES</div>
    (parent and child)
  </div>

  <div class="step-divider abs" style="left:421px"></div>

  <div class="abs step" style="left:428px;width:134px">
    <div class="step-icon" style="background:var(--blue-soft)">
      <svg width="44" height="46" viewBox="0 0 44 46" fill="none" stroke="#1d3f86" stroke-width="1.8" stroke-linejoin="round">
        <rect x="9" y="3" width="20" height="36" rx="3"/><path d="M14 9h10M14 14h10M14 19h6M14 24h8"/>
        <path d="M20 44l-4-10 6-4 4 6V24l6 4 4 16z" fill="#1d3f86"/>
      </svg>
    </div>
    <div class="step-title" style="color:#1d3f86">ONE TWO-HOUR VISIT</div>
    where your child will complete an MRI scan, answer questions about their puberty stage, and have a small hair sample taken to study puberty hormones.
  </div>

  <section class="abs eligibility"></section>
  <div class="abs elig-icon">
    <svg width="40" height="40" viewBox="0 0 40 40" fill="none" stroke="#17a2a0" stroke-width="1.5">
      <circle cx="11" cy="8" r="3.5"/><circle cx="20" cy="6" r="3.5"/><circle cx="29" cy="8" r="3.5"/>
      <path d="M7 24v-8a4 4 0 0 1 8 0v8M16 24v-9a4 4 0 0 1 8 0v9M25 24v-8a4 4 0 0 1 8 0v8"/>
      <path d="M3 28c6 0 9 4 15 4h10l8-5M18 32l-3 4h11"/>
    </svg>
  </div>
  <h2 class="abs elig-title">YOUR CHILD MAY<br>BE ELIGIBLE IF THEY:</h2>
  <div class="abs elig-rule"></div>
  <ul class="abs elig-list">
    <li><svg width="16" height="16" viewBox="0 0 16 16"><circle cx="8" cy="8" r="8" fill="#0e7f7a"/><path d="M4.5 8.2l2.3 2.3 4.7-4.7" fill="none" stroke="#fff" stroke-width="1.8"/></svg>Are age 10-17</li>
    <li><svg width="16" height="16" viewBox="0 0 16 16"><circle cx="8" cy="8" r="8" fill="#0e7f7a"/><path d="M4.5 8.2l2.3 2.3 4.7-4.7" fill="none" stroke="#fff" stroke-width="1.8"/></svg>Tend to worry or overthink negative thoughts</li>
    <li><svg width="16" height="16" viewBox="0 0 16 16"><circle cx="8" cy="8" r="8" fill="#0e7f7a"/><path d="M4.5 8.2l2.3 2.3 4.7-4.7" fill="none" stroke="#fff" stroke-width="1.8"/></svg>Have not been diagnosed with psychosis, learning problems, or autism</li>
  </ul>

  <div class="abs contact-ring"><div class="inner">
    <svg width="30" height="22" viewBox="0 0 30 22" fill="none" stroke="#fff" stroke-width="1.8"><rect x="1" y="1" width="28" height="20"/><path d="M1 1l14 11L29 1M1 21l10-10M29 21L19 11"/></svg>
  </div></div>
  <p class="abs contact-text">INTERESTED IN PARTICIPATING?<br><span class="second">WANT MORE INFORMATION?</span><em>Please contact us!</em></p>
  <div class="abs contact-divider"></div>

  <div class="abs comp-pill"></div>
  <div class="abs gift-ring">
    <svg width="46" height="46" viewBox="0 0 46 46" fill="none" stroke="#0e2457" stroke-width="1.8" stroke-linejoin="round">
      <path d="M23 11c-3-7-11-7-9-1 1 2 5 2 9 1zM23 11c3-7 11-7 9-1-1 2-5 2-9 1z"/>
      <rect x="4" y="11" width="38" height="8"/><rect x="7" y="19" width="32" height="25"/><path d="M23 11v33"/>
      <text x="15" y="38" font-family="Figtree,sans-serif" font-size="14" font-weight="700" fill="#0e2457" stroke="none" text-anchor="middle">$</text>
      <text x="31" y="38" font-family="Figtree,sans-serif" font-size="14" font-weight="700" fill="#0e2457" stroke="none" text-anchor="middle">$</text>
    </svg>
  </div>
  <p class="abs comp-text"><span class="comp-line">COMPENSATION</span><span class="comp-line">UP TO <span class="amount">$140</span></span></p>

  <footer class="abs footer">
    <div class="abs footer-email">
      <svg width="27" height="20" viewBox="0 0 27 20" fill="none" stroke="#fff" stroke-width="1.8"><rect x="1" y="1" width="25" height="18"/><path d="M1 1l12.5 10L26 1M1 19l9-9M26 19l-9-9"/></svg>
      solvestudy@lanternvalley.edu
    </div>
    <div class="abs footer-icons">
      <svg width="24" height="20" viewBox="0 0 24 20" fill="none" stroke="#fff" stroke-width="1.6"><path d="M12 3c-3-3-9-1-9 4 0 3 2 6 5 7v4h4M12 3c3-3 9-1 9 4 0 3-2 6-5 7v4h-4M12 3v15"/></svg>
      <span class="sep"></span>
      <svg width="24" height="20" viewBox="0 0 24 20" fill="none" stroke="#fff" stroke-width="1.6"><path d="M12 18S2 12 2 6.5A5 5 0 0 1 12 5a5 5 0 0 1 10 1.5C22 12 12 18 12 18z"/></svg>
      <span class="sep"></span>
      <svg width="24" height="22" viewBox="0 0 24 22" fill="none" stroke="#fff" stroke-width="1.6"><circle cx="12" cy="6" r="3"/><circle cx="5" cy="10" r="2.5"/><circle cx="19" cy="10" r="2.5"/><path d="M7 20c0-4 2-8 5-8s5 4 5 8M2 19c0-3 1-5 3-5M22 19c0-3-1-5-3-5"/></svg>
    </div>
    <p class="abs footer-note">Your participation helps us understand the developing brain and support adolescent mental health.</p>
  </footer>

</main>
</body>
</html>
```